New profile page for existing party website

For the party website 'Partyvenz' we need a new design for the user profile page.

The page should show
* a profile picture
* basic information like name, age and city
* music styles he/she likes
* links to their Chatterbook profile and website
* a bio (HTML content)
* events they plan to go to
* past events
* pictures

Challenge is that some users may have little information (just their name) while others have a huge description, lots of foto's, events, etc.

Please visit http://www.partyvenz.example and http://www.partyvenz.example/users/bertil

Target Market(s)

Men and women between 18 and 35

Industry/Entity Type

Night Club

Number of Pages Required

2 page

Font styles to use
Other font styles liked:
• Roboto

Requirements
Must have
• Please design how the page looks with a fully filled out profile and with an empty profile.
• It should fit well with the existing website.
• Include designs for both for small screens (mobile) and large screens (tablet, desktop).
Nice to have
• UX design on how to collapse or paginate sections.
• Interactive effects would be a bonus.
Should not have
• The page should not have subnavigation like menus or tabs.

```html
<!DOCTYPE html>
<html lang="nl">
<head>
<meta charset="utf-8">
<title>Partyvenz – Profiel</title>
<link rel="stylesheet" href="https://fonts.googleapis.com/css2?family=Open+Sans:wght@400;600&family=Raleway:wght@400;500&family=Roboto:wght@400;500&display=swap">
<style>
:root{
  --black:#050505;
  --ink:#3a3a3a;
  --text:#6b6b6b;
  --rule:#cfcfcf;
  --band:#ebebeb;
  --dark:#2b2b2b;
  --orange:#f39a1e;
  --white:#ffffff;
  --footer:#161616;
}
*{box-sizing:border-box;margin:0;padding:0}
html,body{width:1200px;height:2426px;overflow:hidden;background:var(--white)}
body{font-family:"Open Sans",Arial,sans-serif;color:var(--text);position:relative}

.site-nav{position:absolute;left:0;top:0;width:1200px;height:91px;background:var(--black);border-bottom:1px solid #333}
.brand{position:absolute;left:100px;top:26px;display:flex;align-items:center;gap:10px;color:var(--white);font-family:"Raleway",sans-serif;font-weight:500;font-size:30px}
.brand-dot{width:12px;height:12px;border-radius:50%;background:var(--white)}
.nav-links{position:absolute;left:638px;top:38px;width:354px;display:flex;justify-content:space-between;list-style:none;font-family:"Roboto",sans-serif;font-size:11.5px;color:var(--white);white-space:nowrap}
.nav-user{position:absolute;left:1004px;top:38px}
.nav-avatar{position:absolute;left:1027px;top:29px;width:32px;height:32px;border-radius:50%;background:linear-gradient(135deg,#b9826b,#5c3a32);border:2px solid #ddd}
.nav-search{position:absolute;left:1065px;top:29px;width:32px;height:32px;border-radius:50%;border:2px solid var(--white);display:flex;align-items:center;justify-content:center}

.profile-hero{position:absolute;left:0;top:91px;width:1200px;height:262px;background:linear-gradient(100deg,#1e2a46 0%,#3c3566 35%,#221c33 60%,#4b3a62 80%,#191a2a 100%)}
.profile-name{position:absolute;left:307px;top:112px;font-family:"Roboto",sans-serif;font-weight:400;font-size:40px;color:var(--white);letter-spacing:.5px}
.profile-meta{position:absolute;left:307px;top:163px;font-size:14px;color:var(--white)}
.profile-meta span{margin:0 8px}
.profile-links{position:absolute;left:310px;top:203px;display:flex;gap:30px;font-size:17px;color:var(--white)}
.profile-links a{display:flex;align-items:center;gap:10px;color:inherit;text-decoration:none}
.sq{width:16px;height:16px;background:var(--white);border-radius:2px}

.profile-bar{position:absolute;left:0;top:353px;width:1200px;height:93px;background:var(--band)}
.profile-intro{position:absolute;left:314px;top:20px;width:360px;font-size:12px;line-height:20px;color:var(--ink)}
.profile-stats{position:absolute;left:728px;top:24px;display:flex;gap:34px;font-size:15px;font-style:italic;color:var(--text)}
.profile-stats span{display:flex;align-items:center;gap:6px}
.profile-avatar{position:absolute;left:100px;top:197px;width:188px;height:188px;border-radius:50%;border:4px solid var(--white);background:radial-gradient(circle at 50% 40%,#c99b82 0%,#8d6957 35%,#e7e2dc 60%,#4a5d72 100%);box-shadow:0 0 0 1px #bbb}

.profile-bio{position:absolute;left:100px;top:500px;width:1005px}
.bio-section{padding-bottom:22px;border-bottom:1px solid var(--rule);margin-bottom:32px}
.bio-section:last-child{border:none}
.bio-section h2{font-family:"Raleway",sans-serif;font-weight:400;font-size:27px;color:var(--ink);margin-bottom:12px}
.bio-section p{font-size:13.5px;line-height:24px;margin-bottom:8px}
.conditions{list-style:none;font-size:13.5px}
.conditions li{position:relative;padding-left:20px;line-height:32px}
.conditions li::before{content:"";position:absolute;left:2px;top:13px;width:6px;height:6px;border-top:1px solid var(--text);border-right:1px solid var(--text);transform:rotate(45deg)}

.plan-events{position:absolute;left:0;top:1423px;width:1200px;height:453px;background:var(--dark)}
.plan-events h2{position:absolute;left:105px;top:58px;font-family:"Raleway",sans-serif;font-weight:400;font-size:29px;color:var(--white)}
.carousel-btn{position:absolute;top:57px;width:30px;height:30px;border-radius:50%;background:#111;display:flex;align-items:center;justify-content:center}
.event-card{position:absolute;top:121px;width:234px}
.event-poster{height:168px;border:3px solid var(--white)}
.event-card h3{margin-top:17px;font-family:"Open Sans",sans-serif;font-weight:600;font-size:20px;color:var(--orange);white-space:nowrap}
.event-card p{font-size:12.5px;line-height:18px;color:#d6d6d6}

.past-events{position:absolute;left:97px;top:1912px;width:500px}
.section-title{font-family:"Raleway",sans-serif;font-weight:400;font-size:31px;color:var(--orange)}
.past-item{position:absolute;width:260px}
.past-item h4{font-weight:400;font-size:15px;color:var(--ink)}
.past-item .city{font-size:13.5px;color:var(--ink);line-height:22px}
.past-item .date{font-size:13.5px;color:var(--orange)}
.view-more{position:absolute;left:276px;top:265px;width:130px;height:40px;background:var(--orange);color:var(--white);font-weight:600;font-size:13px;display:flex;align-items:center;justify-content:center}

.photos{position:absolute;left:631px;top:1912px;width:472px}
.photo-grid{position:absolute;left:3px;top:55px;display:grid;grid-template-columns:repeat(3,146px);gap:14px 11px}
.photo{height:124px;border:3px solid var(--white);box-shadow:0 0 0 1px #ccc}

.site-footer{position:absolute;left:0;top:2285px;width:1200px;height:141px;background:var(--footer);text-align:center}
.footer-links{margin-top:42px;display:flex;justify-content:center;gap:36px;font-family:"Roboto",sans-serif;font-size:15px;color:var(--white)}
.copyright{margin-top:12px;font-size:12px;color:#8a8a8a}
</style>
</head>
<body>

<header class="site-nav">
  <div class="brand"><span class="brand-dot"></span>Partyvenz</div>
  <ul class="nav-links">
    <li>HOME</li><li>AGENDA</li><li>FREE TICKETS</li><li>LOGIN</li><li>PHOTOS</li><li>MY ACCOUNT</li>
  </ul>
  <svg class="nav-user" width="12" height="13" viewBox="0 0 12 13"><circle cx="6" cy="3.5" r="3" fill="#fff"/><path d="M0 13c0-4 3-6 6-6s6 2 6 6z" fill="#fff"/></svg>
  <div class="nav-avatar" role="img" aria-label="Kleine profielfoto van de gebruiker"></div>
  <div class="nav-search"><svg width="12" height="12" viewBox="0 0 12 12"><circle cx="5" cy="5" r="3.6" stroke="#fff" stroke-width="1.8" fill="none"/><path d="M7.7 7.7L11 11" stroke="#fff" stroke-width="1.8"/></svg></div>
</header>

<section class="profile-hero" role="img" aria-label="Achtergrondfoto van een feestmenigte met podiumlichten">
  <h1 class="profile-name">BERTILV PHOTOGRAPHY</h1>
  <p class="profile-meta">Member since : May 24, 2006 <span>/</span> Age : 34 <span>/</span> City : Amsterdam <span>/</span> Music : Latin / Salsa</p>
  <div class="profile-links">
    <a href="#"><svg width="17" height="17" viewBox="0 0 17 17"><circle cx="8.5" cy="8.5" r="7.5" fill="#fff"/><path d="M1 8.5h15M8.5 1c-4 4-4 11 0 15M8.5 1c4 4 4 11 0 15" stroke="#2a2a44" stroke-width="1.2" fill="none"/></svg>Circle</a>
    <a href="#"><span class="sq"></span>Chatterbook</a>
  </div>
</section>

<section class="profile-bar">
  <p class="profile-intro">Nemo enim ipsam voluptatem quia voluptas sit aspernatur aut odit aut fugit, sed quia consequuntur</p>
  <div class="profile-stats">
    <span><svg width="15" height="14" viewBox="0 0 15 14"><path d="M7.5 13L1.6 7A3.5 3.5 0 0 1 7.5 2.4 3.5 3.5 0 0 1 13.4 7z" fill="none" stroke="#777" stroke-width="1.2"/></svg>120 Likes</span>
    <span><svg width="16" height="14" viewBox="0 0 16 14"><path d="M8 1C4 1 1 3.3 1 6.2c0 1.6 1 3 2.5 3.9L3 13l3.4-2C7 11.1 7.5 11.2 8 11.2c4 0 7-2.3 7-5S12 1 8 1z" fill="none" stroke="#777" stroke-width="1.2"/></svg>300 Comments</span>
    <span><svg width="12" height="15" viewBox="0 0 12 15"><rect x="1" y="1" width="10" height="13" fill="none" stroke="#777" stroke-width="1.2"/><path d="M3 5h6M3 8h6M3 11h4" stroke="#777"/></svg>Collecation</span>
  </div>
</section>
<div class="profile-avatar" role="img" aria-label="Profielfoto van de fotograaf"></div>

<main class="profile-bio">
  <section class="bio-section">
    <h2>Wil jij fotograferen voor Partyvenz?</h2>
    <p>Als je uitgaan leuk vindt, makkelijk bent in de omgang en uiteraard houdt van fotograferen, biedt Partyvenz je de kans een kijkje te nemen in de wereld van de partyfotografie. Door de inzet van de fotografen is Partyvenz uitgegroeid tot een van de meest toonaangevende partysites van Nederland. De betrouwbaarheid, de hoge kwaliteit van de foto's en het coveren van de belangrijkste evenementen maakt van Partyvenz een van de best bezochte websites in ons vakgebied</p>
  </section>
  <section class="bio-section">
    <h2>Belangrijk informatie</h2>
    <p>Fotograferen voor Partyvenz is op vrijwillige basis. Je kan kiezen waar en wanneer je uitgaat en foto's maakt, maar een vaste inbreng word wel van je verwacht. Hoe meer je voor Partyvenz doet, hoe meer ervaring je opdoet met de camera en hoe beter je word. Hierdoor kan je weer naar interessantere feesten en festivals. Wat je wel krijgt is gratis entree voor een evenement en soms ook andere voordelen zoals gratis drankjes... Je gaat meestal met ze tweetjes op pad en ontmoet veel nieuwe mensen zoals DJ's en organisatoren. Hoe meer je voor Partyvenz werkt hoe meer ervaring je er ook uit zal halen. De beste fotografen doen de leukste en de meest uitdagende evenementen bijvoorbeeld: Empyrean, Xtremo Open Air, Sunfield weekend, Lagoon Dance etc.</p>
  </section>
  <section class="bio-section">
    <h2>Voorwaarden</h2>
    <ul class="conditions">
      <li>Je moet 18 jaar of ouder zijn.</li>
      <li>Je moet het aankunnen om hoge kwaliteit foto's te maken en professioneel gedrag vertonen.</li>
      <li>Je moet sociaal zijn; een open persoon zijn die ervan houdt om ander e mensen te ontmoeten.</li>
      <li>Het is een vereiste dat je een digitale spiegelreflex-camera hebt en lichtsterke lens met vast diafragma van F2.8 en natuurlijk een externe flitser (E-TTL).</li>
      <li>Je bent verantwoordelijk voor je eigen vervoer om naar de evenementen te gaan waar je foto's maakt.</li>
    </ul>
  </section>
  <section class="bio-section">
    <h2>Aanmelden</h2>
    <p>Wil jij ook het team van Partyvenz versterken en het nachtleven van een andere kant verkennen? Geef je dan op, stuur een mailtje naar bertil@partyvenz.example Vermeld daar goed in je naam, leeftijd, woonplaats en het type camera dat je hebt en je ervaring op het gebied van fotograferen.</p>
    <p>Bekijk ons online foto album voor de door mij geschoten foto's. Bekijk al mijn Vidstream filmpjes via mijn eigen Vidstream kanaal</p>
    <p>www.vidstream.example/user/1982BertilV</p>
  </section>
</main>

<section class="plan-events">
  <h2>Event Plan to Go</h2>
  <div class="carousel-btn" style="left:1039px"><svg width="8" height="10" viewBox="0 0 8 10"><path d="M6 1L2 5l4 4" stroke="#fff" stroke-width="1.6" fill="none"/></svg></div>
  <div class="carousel-btn" style="left:1081px"><svg width="8" height="10" viewBox="0 0 8 10"><path d="M2 1l4 4-4 4" stroke="#fff" stroke-width="1.6" fill="none"/></svg></div>

  <article class="event-card" style="left:102px">
    <div class="event-poster" role="img" aria-label="Kleurrijke festivalposter, 9 juli 2016" style="background:linear-gradient(160deg,#38b44a,#e23b3b 55%,#2a8fd6)"></div>
    <h3>Sis parturient mont</h3>
    <p>nascetur ridiculus mus In iaculis facilisis massa Etiam eu urna Sed porta Suspendisse quam leo</p>
  </article>
  <article class="event-card" style="left:357px">
    <div class="event-poster" role="img" aria-label="Mintgroene festivalposter" style="background:linear-gradient(160deg,#a7dcc6,#7cc9ac)"></div>
    <h3>Phasellus pellent</h3>
    <p>nascetur ridiculus mus In iaculis facilisis massa Etiam eu urna Sed porta Suspendisse quam leo</p>
  </article>
  <article class="event-card" style="left:611px">
    <div class="event-poster" role="img" aria-label="Gele festivalafbeelding op witte achtergrond" style="background:radial-gradient(circle,#f3d21c 0%,#e9bd10 45%,#ffffff 47%)"></div>
    <h3>Sed porta Suspendisse</h3>
    <p>nascetur ridiculus mus In iaculis facilisis massa Etiam eu urna Sed porta Suspendisse quam leo</p>
  </article>
  <article class="event-card" style="left:864px">
    <div class="event-poster" role="img" aria-label="Tropische festivalposter, 28 mei 2016" style="background:linear-gradient(170deg,#2db1c9,#7fc34a 55%,#f0a41e)"></div>
    <h3>Cras a ante vitae</h3>
    <p>nascetur ridiculus mus In iaculis facilisis massa Etiam eu urna Sed porta Suspendisse quam leo</p>
  </article>
</section>

<section class="past-events">
  <h2 class="section-title">Past Events</h2>
  <div class="past-item" style="left:3px;top:70px"><h4>FESTIVAL TODO MUNDO 2016</h4><div class="city">Rotterdam</div><div class="date">25 March 2016</div></div>
  <div class="past-item" style="left:276px;top:70px"><h4>DONEC CONVALLIs&nbsp; 2016</h4><div class="city">Rotterdam</div><div class="date">15 March 2016</div></div>
  <div class="past-item" style="left:3px;top:154px"><h4>RHONCUS DICTUM&nbsp; 2016</h4><div class="city">Rotterdam</div><div class="date">23 March 2016</div></div>
  <div class="past-item" style="left:276px;top:154px"><h4>ALIQUAM ERAT VOLUTPA 2016</h4><div class="city">Rotterdam</div><div class="date">10 March 2016</div></div>
  <div class="past-item" style="left:3px;top:243px"><h4>CRAS A ANTE VITAE ENIM&nbsp; O 2016</h4><div class="city">Rotterdam</div><div class="date">22 March 2016</div></div>
  <div class="view-more">VIEW MORE</div>
</section>

<section class="photos">
  <h2 class="section-title">Photos</h2>
  <div class="photo-grid">
    <div class="photo" role="img" aria-label="Feestfoto van bezoekers in oranje" style="background:linear-gradient(150deg,#5a4335,#d9772b 60%,#3a2c24)"></div>
    <div class="photo" role="img" aria-label="Feestfoto van een straatfeest" style="background:linear-gradient(150deg,#c9c2b8,#d87a3a 55%,#8a7e72)"></div>
    <div class="photo" role="img" aria-label="Feestfoto van lachende bezoekers" style="background:linear-gradient(150deg,#e6b04a,#c8642a 55%,#6b4a36)"></div>
    <div class="photo" role="img" aria-label="Feestfoto van twee bezoekers" style="background:linear-gradient(150deg,#f0ede8,#9a6a4e 50%,#e0803a)"></div>
    <div class="photo" role="img" aria-label="Feestfoto van twee mannen" style="background:linear-gradient(150deg,#2a2624,#7b5444 55%,#1c1a19)"></div>
    <div class="photo" role="img" aria-label="Feestfoto van bezoekers met oranje hoed" style="background:linear-gradient(150deg,#9aa6b6,#a5704f 50%,#e17c2e)"></div>
  </div>
</section>

<footer class="site-footer">
  <nav class="footer-links"><span>CONTACT</span><span>TERMS OF USE</span><span>PRIVACY POLICY</span></nav>
  <p class="copyright">© 2016 Company Name&nbsp; All right reserved</p>
</footer>

</body>
</html>
```